Sustainably Transforming Education

Company is education services based. early learning through adult and corporate. Focus is national government policy and program design and delivery alongside a research based and academically grounded set of approaches to planning, evaluation, and change management.I am looking for an innovative design position that aligns with the global agendas for innovation, creativity and collaboration at international and national policy levels (berulo is a name that reflects these qualities - colours need to reflect amythyst in some way). I also need a design that translates from a business card as 1 medium of interaction to a template that can work in word/powerpoint etc to support both stationery as well as a digital strategy across multiple channels (fb/twit/etc)There is no slogan/tag line for the company and their is no logo. I was looking to just leverage the name - have currently played around with various fonts (ending up with cuisine - all lowercase).

Industry/Entity Type

Adult

Contact Information for Business Card

name: berulo (all lowercase)Chairman: Andrew CrowMobile: +61 418 902 131Web: www.berulo.comemail: martin.pelly@berulo-example.com

Font styles to use
Script
Other font styles liked:
• cuisine

Colors
e34298
e667a6
33a6d7
aaaaaa

Requirements
Nice to have
• https://files.example-share.net/sh/qx7kw2hd91lzmnp/AAFr3tYbQeLp8VwZnKcDs2Hu?dl=0
• Link to the printwell templates used to begin this process....the one with the lines was about people intersecting (collaborating).....the organic shapes one more of a fluid feel of people coming together - the overall shape being largely spherical could represent a "global" feel.....anyway that is how I was thinking about these

```html
<!DOCTYPE html>
<html lang="en">
<head>
<meta charset="utf-8">
<title>Martin Pelly – berulo business card</title>
<link rel="stylesheet" href="https://fonts.googleapis.com/css2?family=Courgette&display=swap">
<style>
  :root {
    --ink-night: #0d0a1c;
    --amethyst-blue: #5a55b8;
    --amethyst-violet: #7a4fa8;
    --berry: #e34298;
    --berry-soft: #e667a6;
    --band: rgba(46, 46, 46, 0.94);
    --band-light: rgba(70, 70, 70, 0.92);
    --text-light: #ffffff;
    --script: "Courgette", cursive;
  }
  html, body {
    margin: 0;
    padding: 0;
    overflow: hidden;
    background: #ffffff;
  }
  .card {
    position: relative;
    width: 1200px;
    height: 740px;
    overflow: hidden;
    font-family: var(--script);
    color: var(--text-light);
  }
  .card__artwork {
    position: absolute;
    inset: 0;
    width: 100%;
    height: 100%;
  }
  .band {
    position: absolute;
    right: 0;
    box-sizing: border-box;
    display: flex;
    align-items: center;
    background: var(--band);
  }
  .band--name {
    top: 82px;
    left: 460px;
    height: 106px;
    padding-left: 34px;
  }
  .holder-name {
    margin: 0;
    font-size: 86px;
    font-weight: 400;
    line-height: 1;
    letter-spacing: 1px;
  }
  .band--title {
    top: 196px;
    left: 870px;
    height: 60px;
    padding-left: 18px;
  }
  .holder-title {
    margin: 0;
    font-size: 40px;
    font-weight: 400;
    letter-spacing: 2px;
  }
  .contact {
    margin: 0;
    padding: 0;
    list-style: none;
  }
  .band--contact {
    justify-content: flex-end;
    padding-right: 78px;
    font-size: 23px;
    letter-spacing: 2px;
  }
  .band--phone { top: 494px; left: 862px; height: 44px; }
  .band--email { top: 542px; left: 570px; height: 41px; background: var(--band-light); }
  .band--web   { top: 583px; left: 720px; height: 41px; }
</style>
</head>
<body>
  <main class="card">
    <svg class="card__artwork" viewBox="0 0 1200 740" preserveAspectRatio="none" role="img" aria-label="Abstract network of intersecting blue, violet and magenta lines on a dark background">
      <defs>
        <radialGradient id="glow-violet" cx="0.3" cy="0.35" r="0.6">
          <stop offset="0" stop-color="var(--amethyst-violet)" stop-opacity="0.85"/>
          <stop offset="1" stop-color="var(--amethyst-violet)" stop-opacity="0"/>
        </radialGradient>
        <radialGradient id="glow-berry" cx="0.75" cy="0.7" r="0.55">
          <stop offset="0" stop-color="var(--berry)" stop-opacity="0.6"/>
          <stop offset="1" stop-color="var(--berry)" stop-opacity="0"/>
        </radialGradient>
        <radialGradient id="glow-blue" cx="0.55" cy="0.1" r="0.6">
          <stop offset="0" stop-color="var(--amethyst-blue)" stop-opacity="0.8"/>
          <stop offset="1" stop-color="var(--amethyst-blue)" stop-opacity="0"/>
        </radialGradient>
      </defs>
      <rect width="1200" height="740" fill="var(--ink-night)"/>
      <rect width="1200" height="740" fill="url(#glow-blue)"/>
      <rect width="1200" height="740" fill="url(#glow-violet)"/>
      <rect width="1200" height="740" fill="url(#glow-berry)"/>
    </svg>

    <header>
      <div class="band band--name"><h1 class="holder-name">Martin Pelly</h1></div>
      <div class="band band--title"><p class="holder-title">Chairman</p></div>
    </header>

    <ul class="contact">
      <li class="band band--contact band--phone">+61 427 315 086</li>
      <li class="band band--contact band--email">martin.pelly@berulo-example.com</li>
      <li class="band band--contact band--web">www.berulo-example.com</li>
    </ul>
  </main>
</body>
</html>
```